Backdrop for Wobbly Mabel the Clown

I need a backdrop design drawn with stage curtains. I am a professional clown. My photo of me as a clown is attached. Do not put my face on the backdrop. I mainly perform at birthday parties in living rooms. I am going to have a backdrop printed that is 8 feet by 8 feet (243.84 centimeters by 243.84 centimeters). My printing company says it needs to be vector. The backdrop will be behind me as I perform a funny magic show for kids ages 3 to 7. I have attached designs of backdrops with curtains. I don't want the people.
* I am not sure if I want a floor drawn, so I would like to see some designs with a floor, and some without.
* I want it to look very much like a cartoon. The ones I attached with the red curtains are not cartoony enough. Maybe a backdrop that looks like it is from a Mr. Plimble book or Pebble Tom. I love the style of the one with the man in front, and if you drew my curtains very similar to that one, I might pick your design.
* I like the color scheme of my logo. Orange, red, yellow, and turquoise. Black and white also work. If those are not enough colors for you, the one color you could add is pink, because it ties into my hair color.
* I think for the middle part, turquoise would be a good color.
For the middle part, I do not want it too busy. It could be plain, or a gradient, or maybe a dark turquoise background and a light turquoise design, for example, swirls; you know best. During my performance, photos that are taken in front of the backdrop will mainly focus on the middle, thus I would rather have the detailed part be the curtains, which will be to the side and top. I don't recommend orange or pink for the middle part because my hair or pants will be less noticeable. Although my vest is turquoise, I think that is okay. Turquoise is my favorite color. I would like the turquoise to have the correct blue and green mixture to match the turquoise in my logo, but it could be darker or lighter.
* Shades of most colors might look more fun if some were a little lighter than my logo colors. But for the behind the curtains part, it might look more three dimensional if that was darker, but your the experts, maybe I'm wrong.
* I am undecided if I want to have my logo on the backdrop. So maybe make one design with and one without. This is one reason why I attached my logo, so you can see how it looks on my backdrop. I might be more likely to choose your design if it went with my logo, so maybe some polka dots or diagonal stripes like my logo has. I wear my logoed nametag when I perform, and my logo is on my case of magic which I have on stage
* You could design a new Wobbly Mabel logo to put on my backdrop, and if I choose your backdrop, I might hire you to make me a new logo. I am happy with my logo, but I could be wowed with something else. I do not always perform as a clown. I sometimes perform plain-clothes, thus don't put the word "clown" on my backdrop. I always have a chicken on my head, which is why I suggested to my last logo designer to include a chicken. But you could just write out my name with whimsical lettering no chicken. Or use my current logo. Or no wording at all.
* I would like at least half of the backdrop to be the behind the curtain part. So the curtains will need to either be narrower than some of my attachments or have the gather point towards the top.
* In a few months, I will buy a skinny table to be used in my show, and if I chose your design, I would later hire you to design for me a table wrap.

Update April 29: I added a picture of chicken headbands because one of the designers asked. I always wear one of the headbands pictured. If I make a child a chicken that is not on a headband, I put the chicken's feet together. Putting a chicken on the backdrop is not a must-have.

Target Market(s)

Kids ages three to seven

Industry/Entity Type

Entertainment

Colors
faa54b
ec1f27
fbee3e
33b8a4
00a990
86cfc6
f78f20
e667a6
f04a50

Requirements
Must have
• The illusion of a cheerful cartoon stage.
The part between the curtains needs to be simple. For example, the stripe photo I uploaded today. No blue
Do one of these options for middle:
have a light turquoise and a dark turquoise
or have a light turquoise, dark turquoise, and one more color of stars or polka dots or confetti.

Must have a simple cartoon style. The style of the cartoon screenshots I uploaded today. For example, a theater stage from the tv show “The Farrows” or the tv show “Toffee Hen.”
Nice to have
• April 26 Update: If you use my name logo, I would probably like my name better if it was at the top. Either in the top center, or hanging diagonal in the left corner. Because if the name is lower, then I will be standing in front of it and blocking my name from the audience. I am still undecided if I want my name logo on my backdrop.
April 27 update. The photo of me is so you know what I look like. I do not want that photo on my backdrop.
Update April 28: Today I uploaded a photo to show you how I will use the backdrop. This is a picture of a colleague. Her backdrop is satisfactory. I want my backdrop to look less elegant.
Update April 28: Do not use my clown face because sometimes I perform magic shows plain-clothes.
Do not use the color blue. My logo and costume are red, yellow, orange, and turquoise. I want the backdrop to go with my color scheme. If you need a 4th color, use pink. Black, white, and grey are good colors.

Update April 30: The part between the curtains needs to be simple. For example, the stripe photo I uploaded today. No blue

April 30 update: Must have a simple cartoon style. The style of the cartoon screenshots I uploaded today. For example, a theater stage from the tv show “The Farrows” or the tv show “Toffee Hen.” I might choose your design if the curtains looked like the curtains were on a stage in “The Farrows” tv show.

May 1 update: Make the back drop look hand drawn. Do not make it look computer designed. I know you are using a computer, but give the illusion that the backdrop was drawn by hand. For example “The Farrows” tv show. I posted a screen shot of scenes from the tv show I like.
Should not have
• Don't make it look realistic. Make it look like a cartoon.

*Do not include my face on the backdrop. Today, April 28, I uploaded 2 photos of my face because a designer asked. No face on the backdrop.

* Do not include the color blue or green or purple. no blue, no green, no purple.

* Do not have a detailed background. Do not put many colors between the curtains. You may make the top and sides either simple or detailed. Make the middle simple. For example, on April 30 I uploaded stripes in the style I want. But turquoise and darker. Not blue.

```html
<!DOCTYPE html>
<html lang="en">
<head>
<meta charset="utf-8">
<title>Wobbly Mabel Stage Backdrop</title>
<link rel="stylesheet" href="https://fonts.googleapis.com/css2?family=Chewy&display=swap">
<style>
  :root {
    --wing-teal: #00a990;
    --wall-teal: #33b8a4;
    --wall-light: #86cfc6;
    --spot-white: #ffffff;
    --curtain-red: #ec1f27;
    --curtain-deep: #a8141a;
    --curtain-light: #f04a50;
    --tieback-red: #c3161d;
    --floor-brown: #7a4a2c;
    --floor-dark: #4e2c18;
    --name-red: #ec1f27;
  }
  html, body {
    margin: 0;
    padding: 0;
    width: 1200px;
    height: 1200px;
    overflow: hidden;
    background: var(--wing-teal);
  }
  .backdrop {
    position: relative;
    width: 1200px;
    height: 1200px;
    overflow: hidden;
  }
  .stage-art {
    position: absolute;
    inset: 0;
    width: 1200px;
    height: 1200px;
    display: block;
  }
  .performer-name {
    position: absolute;
    left: 0;
    right: 0;
    top: 418px;
    margin: 0;
    text-align: center;
    font-family: "Chewy", sans-serif;
    font-weight: 400;
    font-size: 112px;
    line-height: 1;
    letter-spacing: 3px;
    color: var(--name-red);
  }
</style>
</head>
<body>
<main class="backdrop">
  <svg class="stage-art" viewBox="0 0 1932 1932" xmlns="http://www.w3.org/2000/svg">
    <defs>
      <radialGradient id="spotlight" cx="970" cy="1000" r="800" gradientUnits="userSpaceOnUse">
        <stop offset="0" stop-color="var(--spot-white)"/>
        <stop offset="0.35" stop-color="var(--wall-light)"/>
        <stop offset="1" stop-color="var(--wall-teal)"/>
      </radialGradient>
      <linearGradient id="curtainLeft" x1="0" y1="0" x2="1" y2="0">
        <stop offset="0" stop-color="var(--curtain-deep)"/>
        <stop offset="0.55" stop-color="var(--curtain-red)"/>
        <stop offset="1" stop-color="var(--curtain-light)"/>
      </linearGradient>
      <linearGradient id="curtainRight" x1="1" y1="0" x2="0" y2="0">
        <stop offset="0" stop-color="var(--curtain-deep)"/>
        <stop offset="0.55" stop-color="var(--curtain-red)"/>
        <stop offset="1" stop-color="var(--curtain-light)"/>
      </linearGradient>
      <linearGradient id="valance" x1="0" y1="0" x2="0" y2="1">
        <stop offset="0" stop-color="var(--curtain-deep)"/>
        <stop offset="1" stop-color="var(--curtain-red)"/>
      </linearGradient>
      <linearGradient id="floorboards" x1="0" y1="0" x2="0" y2="1">
        <stop offset="0" stop-color="var(--floor-dark)"/>
        <stop offset="1" stop-color="var(--floor-brown)"/>
      </linearGradient>
    </defs>

    <rect class="side-wing" x="0" y="0" width="1932" height="1932" fill="var(--wing-teal)"/>
    <rect class="back-wall" x="380" y="0" width="1170" height="1762" fill="url(#spotlight)"/>
    <path class="stage-floor" role="img" aria-label="Wooden stage floor"
          d="M375 1762 L1552 1762 L1932 1932 L0 1932 Z" fill="url(#floorboards)"/>

    <path class="curtain curtain-left" role="img" aria-label="Red stage curtain gathered to the left"
          d="M0 0 L470 0 C440 440 340 790 178 995 C155 1025 142 1045 146 1072
             C168 1185 192 1310 195 1395 C150 1450 80 1495 0 1525 Z"
          fill="url(#curtainLeft)"/>
    <path class="tieback tieback-left" d="M0 962 L186 992 L176 1050 L0 1022 Z" fill="var(--tieback-red)"/>

    <path class="curtain curtain-right" role="img" aria-label="Red stage curtain gathered to the right"
          d="M1932 0 L1462 0 C1492 440 1592 790 1754 995 C1777 1025 1790 1045 1786 1072
             C1764 1185 1740 1310 1737 1395 C1782 1450 1852 1495 1932 1525 Z"
          fill="url(#curtainRight)"/>
    <path class="tieback tieback-right" d="M1932 962 L1746 992 L1756 1050 L1932 1022 Z" fill="var(--tieback-red)"/>

    <path class="valance valance-side" role="img" aria-label="Red curtain valance across the top"
          d="M0 0 L1932 0 L1932 150 C1890 190 1840 200 1790 185 C1740 205 1680 200 1630 180
             C1580 200 1520 195 1470 170 L460 170
             C410 195 350 200 300 180 C250 200 190 205 140 185 C90 200 40 190 0 150 Z"
          fill="url(#valance)"/>
    <path class="valance valance-centre" role="img" aria-label="Red centre curtain swag"
          d="M490 0 L1440 0 C1430 120 1410 190 1370 215 C1330 235 1300 225 1270 255
             C1230 290 1180 300 1140 290 C1100 315 1060 320 1020 312
             C980 332 940 338 900 322 C860 328 810 318 770 298
             C730 300 690 282 660 252 C625 228 590 232 560 210 C520 170 500 90 490 0 Z"
          fill="var(--curtain-red)"/>
  </svg>

  <h1 class="performer-name">Wobbly Mabel</h1>
</main>
</body>
</html>
```